Velk Partners Building Business Cards

We need a business card that reflects our business as "Solar Experts" in San Diego. Browse our website www.velkpartners.example our License needs to be displayed as "CSLB# 3867140" our phone number is (619) 555-0187

Save thousands on your electric bills and increase the value of your home while helping to protect the environment. Our solar installation experts will help you design the system that's right for you, using only the highest quality equipment that will look great and give you ideal performance. Our goal is to make you energy independent, and get your electric bill to 0.

Paul Osterby
(619) 555-0187
paul@velkpartners.example

Target Market(s)

Home owners in san diego looking for solar

Industry/Entity Type

Solar Energy

Contact Information for Business Card

Paul Osterby
(619) 555-0187
paul@velkpartners.example

Font styles to use
Other font styles liked:
• Use our logo font

Requirements
Must have
• License needs to be displayed as "CSLB# 3867140" our phone number is (619) 555-0187
Nice to have
• Real images of rooftop home solar in san diego
Should not have
• our business address

```html
<!DOCTYPE html>
<html lang="en">
<head>
<meta charset="utf-8">
<title>Velk Partners Building – Business Card</title>
<link rel="stylesheet" href="https://fonts.googleapis.com/css2?family=Source+Sans+3:wght@400;600;700&display=swap">
<style>
  :root {
    --stage: #dcd7d1;
    --card: #f5f2ee;
    --navy: #1d2a5c;
    --navy-deep: #141d45;
    --orange: #e8921c;
    --orange-light: #f5b04a;
    --ink-light: #e9ddd0;
    --ink-soft: #d7d9e4;
  }
  * { margin: 0; padding: 0; box-sizing: border-box; }
  html, body {
    width: 1200px;
    height: 969px;
    overflow: hidden;
    background: var(--stage);
    font-family: "Source Sans 3", "Myriad Pro", Arial, sans-serif;
  }
  .business-card {
    position: absolute;
    left: 100px;
    top: 199px;
    width: 1000px;
    height: 571px;
    border-radius: 34px;
    overflow: hidden;
    background: var(--card);
    box-shadow: 0 18px 40px rgba(0,0,0,0.18);
  }
  .card-waves {
    position: absolute;
    inset: 0;
    width: 1000px;
    height: 571px;
  }
  .company-name {
    position: absolute;
    left: 62px;
    top: 78px;
    font-size: 56px;
    font-weight: 700;
    letter-spacing: -0.5px;
    color: var(--navy);
    line-height: 1;
  }
  .holder {
    position: absolute;
    left: 52px;
    top: 460px;
  }
  .holder-name {
    font-size: 34px;
    font-weight: 600;
    color: var(--ink-light);
    line-height: 1.1;
  }
  .holder-title {
    font-size: 26px;
    font-weight: 400;
    color: var(--orange);
    line-height: 1.3;
  }
  .contact-list {
    position: absolute;
    right: 52px;
    top: 328px;
    list-style: none;
    text-align: right;
  }
  .contact-list li {
    display: flex;
    justify-content: flex-end;
    align-items: center;
    gap: 12px;
    font-size: 24px;
    color: var(--ink-soft);
    height: 37px;
  }
  .contact-list .license {
    margin-bottom: 26px;
    padding-right: 34px;
  }
  .contact-icon {
    width: 22px;
    height: 22px;
    flex: none;
  }
</style>
</head>
<body>
  <div class="business-card">
    <svg class="card-waves" viewBox="0 0 1000 571" aria-hidden="true">
      <defs>
        <linearGradient id="navyBand" x1="0" y1="0" x2="0" y2="1">
          <stop offset="0" stop-color="var(--navy)"/>
          <stop offset="1" stop-color="var(--navy-deep)"/>
        </linearGradient>
        <linearGradient id="orangeStripe" x1="0" y1="0" x2="1" y2="0">
          <stop offset="0" stop-color="var(--orange)"/>
          <stop offset="0.6" stop-color="var(--orange-light)"/>
          <stop offset="1" stop-color="var(--orange)"/>
        </linearGradient>
      </defs>
      <!-- main navy band -->
      <path d="M0 368 C 110 410, 200 428, 330 400 C 480 368, 650 262, 800 262 C 880 262, 950 300, 1000 340 L1000 571 L0 571 Z" fill="url(#navyBand)"/>
      <!-- thin navy accent line -->
      <path d="M0 352 C 110 392, 200 410, 330 382 C 480 350, 650 240, 790 238 C 870 237, 950 275, 1000 312 L1000 322 C 950 286, 870 250, 790 252 C 650 256, 480 364, 330 396 C 200 424, 110 406, 0 366 Z" fill="var(--navy)"/>
      <!-- orange stripe -->
      <path d="M0 330 C 110 372, 200 392, 320 366 C 470 330, 640 216, 780 212 C 870 210, 950 250, 1000 290 L1000 306 C 950 266, 870 228, 780 230 C 640 236, 470 350, 320 384 C 200 410, 110 390, 0 346 Z" fill="url(#orangeStripe)"/>
    </svg>

    <div class="company-name">Velk Partners Building</div>

    <div class="holder">
      <p class="holder-name">Paul Osterby</p>
      <p class="holder-title">CFO/Founder</p>
    </div>

    <ul class="contact-list">
      <li class="license">CSLB# 3867140</li>
      <li>(619) 555-0187
        <svg class="contact-icon" viewBox="0 0 24 24" aria-hidden="true"><path fill="var(--orange)" d="M6.6 2.5l3 3.6-1.9 2.4c1.3 2.8 3.4 4.9 6.2 6.2l2.4-1.9 3.6 3-1.6 3.3c-8.4-.5-14.9-7-15.4-15.4z"/></svg>
      </li>
      <li>paul@velkpartners.example
        <svg class="contact-icon" viewBox="0 0 24 24" aria-hidden="true"><rect x="2" y="5" width="20" height="14" rx="1.5" fill="var(--orange)"/><path d="M2.5 6l9.5 7 9.5-7" fill="none" stroke="var(--navy)" stroke-width="1.6"/></svg>
      </li>
      <li>www.velkpartners.example
        <svg class="contact-icon" viewBox="0 0 24 24" aria-hidden="true"><circle cx="12" cy="12" r="10" fill="var(--orange)"/><path d="M2 12h20M12 2c3 3 3 17 0 20M12 2c-3 3-3 17 0 20" fill="none" stroke="var(--navy)" stroke-width="1.4"/></svg>
      </li>
    </ul>
  </div>
</body>
</html>
```